Harlow Advisory, Business Cards for International Development Consultancy

I'm an independent consultant working in the international development sector. I work with small organisations in developing countries to help them develop their community based programs so that they can be internationally competitive. This means they need to work better with their own communities to deliver meaningful quality work and also improve the accountability of their work so that they can compete for international and domestic funding.

I like the idea of being a connector between community, local organisations and international best practice and back again (ie acknowledging that international best practice can learn a lot from community).

My surname is Harlow - so I'd like the logo to use the idea of web as a connector.

I work with people with sight impairments - would like my card to be useful for low vision (i.e. clear graphics, easy to read font) and no vision (i.e. brail).

Target Market(s)

international non-government organisations (i.e. pelmark, lift the hamlets, kindred arc), Blue Shield Gold Lantern, government (i.e. Australian Bureau of Overseas Relations, consulars), non government agencies,

Industry/Entity Type

Business

Contact Information for Business Card

International Development Consultant
Connecting International Development with Community

Marcia Harlow
Lead Consultant
Phone: +61 412 583720
Email: mharlow.advisory@postnest.example

Font styles to use
Sans Serif

Colors
eaf1f7
85acd3
d3a5cc
0456a4
a64599
0255a3

Requirements
Nice to have
• brail
Should not have
• fancy fonts - needs to be easy to read.

```html
<!DOCTYPE html>
<html lang="en">
<head>
<meta charset="utf-8">
<title>Harlow Advisory – Business Cards</title>
<link rel="stylesheet" href="https://fonts.googleapis.com/css2?family=Open+Sans:wght@400;600;700&display=swap">
<style>
  :root {
    --stage: #eaf1f7;
    --card-white: #ffffff;
    --deep-blue: #0456a4;
    --core-blue: #0255a3;
    --soft-blue: #85acd3;
    --plum: #a64599;
    --soft-plum: #d3a5cc;
    --ink: #6f7276;
    --ink-dark: #5e6266;
    --logo-white: #ffffff;
    --braille-dot: #c9cfd6;
  }
  * { box-sizing: border-box; margin: 0; padding: 0; }
  html, body {
    width: 1200px;
    height: 800px;
    overflow: hidden;
    background: var(--stage);
    font-family: "Open Sans", Arial, sans-serif;
  }
  .canvas { position: relative; width: 1200px; height: 800px; }

  /* Back of card */
  .card-back {
    position: absolute;
    left: 80px;
    top: 80px;
    width: 366px;
    height: 640px;
    overflow: hidden;
    box-shadow: 0 6px 18px rgba(0,0,0,0.18);
  }
  .card-back__art {
    position: absolute;
    inset: 0;
    background:
      linear-gradient(150deg, var(--soft-blue) 0%, transparent 38%),
      linear-gradient(25deg, var(--plum) 0%, transparent 42%),
      linear-gradient(200deg, var(--core-blue) 0%, var(--deep-blue) 40%, #3f7cc0 70%, #6a5cad 100%);
  }
  .card-back__logo {
    position: absolute;
    left: 50%;
    top: 64%;
    transform: translate(-50%, -50%) rotate(90deg);
    color: var(--logo-white);
    font-weight: 700;
    white-space: nowrap;
    line-height: 1;
  }
  .card-back__logo-main {
    display: block;
    font-size: 68px;
    letter-spacing: 6px;
  }
  .card-back__logo-sub {
    display: block;
    font-size: 33px;
    letter-spacing: 8px;
    margin-top: 4px;
  }

  /* Front of card */
  .card-front {
    position: absolute;
    left: 480px;
    top: 217px;
    width: 640px;
    height: 366px;
    background: var(--card-white);
    overflow: hidden;
    box-shadow: 0 6px 18px rgba(0,0,0,0.18);
  }
  .card-front__art {
    position: absolute;
    inset: 0;
    clip-path: polygon(24% 0, 100% 0, 100% 100%, 80% 100%, 94% 62%, 66% 48%, 56% 18%, 40% 9%);
    background:
      radial-gradient(ellipse at 40% 6%, rgba(255,255,255,1) 0%, rgba(255,255,255,0.55) 22%, transparent 45%),
      radial-gradient(ellipse at 78% 78%, rgba(255,255,255,0.8) 0%, transparent 32%),
      linear-gradient(160deg, var(--soft-plum) 0%, var(--plum) 30%, var(--soft-blue) 55%, var(--deep-blue) 100%);
  }
  .contact-list {
    position: absolute;
    left: 34px;
    top: 34px;
    list-style: none;
    font-size: 12px;
    color: var(--ink);
  }
  .contact-list li {
    display: flex;
    align-items: center;
    gap: 6px;
    line-height: 17px;
  }
  .contact-list svg { width: 11px; height: 11px; flex: none; }
  .identity {
    position: absolute;
    left: 270px;
    top: 140px;
  }
  .identity__name {
    font-size: 30px;
    font-weight: 400;
    letter-spacing: 1px;
    color: var(--plum);
    line-height: 1;
  }
  .identity__role {
    margin-top: 8px;
    font-size: 14px;
    font-weight: 600;
    letter-spacing: 1.5px;
    color: var(--ink-dark);
  }
  .address {
    position: absolute;
    left: 270px;
    top: 262px;
    font-size: 13px;
    font-style: normal;
    letter-spacing: 1px;
    color: var(--ink-dark);
    line-height: 19px;
  }
  .braille {
    position: absolute;
    left: 34px;
    top: 308px;
    width: 96px;
    height: 20px;
  }
</style>
</head>
<body>
<main class="canvas">

  <section class="card-back" aria-label="Card back">
    <div class="card-back__art" role="img" aria-label="Blue and plum faceted background"></div>
    <div class="card-back__logo">
      <span class="card-back__logo-main">HARLOW</span>
      <span class="card-back__logo-sub">ADVISORY</span>
    </div>
  </section>

  <section class="card-front" aria-label="Card front">
    <div class="card-front__art" role="img" aria-label="Plum and blue faceted graphic fading to white"></div>

    <ul class="contact-list">
      <li>
        <svg viewBox="0 0 12 12" aria-hidden="true"><circle cx="6" cy="6" r="6" fill="var(--plum)"/><path d="M4 3.2l1 1.6-.6.7a4 4 0 0 0 2.1 2.1l.7-.6 1.6 1-.5 1A5 5 0 0 1 3 4.2z" fill="#fff"/></svg>
        +61 412 583720
      </li>
      <li>
        <svg viewBox="0 0 12 12" aria-hidden="true"><circle cx="6" cy="6" r="6" fill="var(--plum)"/><rect x="3" y="4" width="6" height="4.2" fill="none" stroke="#fff" stroke-width="0.9"/><path d="M3 4l3 2.3L9 4" fill="none" stroke="#fff" stroke-width="0.9"/></svg>
        mharlow.advisory@postnest.example
      </li>
      <li>
        <svg viewBox="0 0 12 12" aria-hidden="true"><circle cx="6" cy="6" r="6" fill="var(--plum)"/><circle cx="6" cy="6" r="3.2" fill="none" stroke="#fff" stroke-width="0.8"/><path d="M2.8 6h6.4M6 2.8c-1.6 2-1.6 4.4 0 6.4M6 2.8c1.6 2 1.6 4.4 0 6.4" fill="none" stroke="#fff" stroke-width="0.7"/></svg>
        www.harlowadvisory.example
      </li>
    </ul>

    <div class="identity">
      <h1 class="identity__name">MARCIA HARLOW</h1>
      <p class="identity__role">LEAD CONSULTANT</p>
    </div>

    <address class="address">
      4482 FERNBROOK LANE #207<br>
      UPPER ASHFORD, MD 20913, USA
    </address>

    <svg class="braille" viewBox="0 0 96 20" role="img" aria-label="Braille: harlow">
      <g fill="var(--braille-dot)">
        <!-- h: 1 2 5 -->
        <circle cx="3" cy="3" r="1.6"/><circle cx="3" cy="9" r="1.6"/><circle cx="8" cy="9" r="1.6"/>
        <!-- a: 1 -->
        <circle cx="19" cy="3" r="1.6"/>
        <!-- r: 1 2 3 5 -->
        <circle cx="35" cy="3" r="1.6"/><circle cx="35" cy="9" r="1.6"/><circle cx="35" cy="15" r="1.6"/><circle cx="40" cy="9" r="1.6"/>
        <!-- l: 1 2 3 -->
        <circle cx="51" cy="3" r="1.6"/><circle cx="51" cy="9" r="1.6"/><circle cx="51" cy="15" r="1.6"/>
        <!-- o: 1 3 5 -->
        <circle cx="67" cy="3" r="1.6"/><circle cx="67" cy="15" r="1.6"/><circle cx="72" cy="9" r="1.6"/>
        <!-- w: 2 4 5 6 -->
        <circle cx="83" cy="9" r="1.6"/><circle cx="88" cy="3" r="1.6"/><circle cx="88" cy="9" r="1.6"/><circle cx="88" cy="15" r="1.6"/>
      </g>
    </svg>
  </section>

</main>
</body>
</html>
```